Telecommunications Company needs a business card design

We are looking for a sleek, professional and modern business card design based off our new logo. Will look at both light and dark options. On some designs please provide a small space for a QR code

Target Market(s)

B2B clients in Australia

Contact Information for Business Card

Name, Position, Brisbane (head) office, Phone number, email address, QR code (link to our website qlinetelecom.com.au

Colors
0054AA
0677BA
7BADD7
CADEEF
E8F1F8
0094D4
00A9DD
6FCCEA
C7EBF8
E9F6FB
00AB8E
00BBA5
67D7C9
C6EFE9
E9F9F6

```html
<!DOCTYPE html>
<html lang="en">
<head>
<meta charset="utf-8">
<title>Qline Telecom – Business Cards</title>
<link rel="stylesheet" href="https://fonts.googleapis.com/css2?family=Montserrat:wght@400;500;600;700&display=swap">
<style>
  :root {
    --blue-deep: #0054AA;
    --blue: #0677BA;
    --blue-bright: #0094D4;
    --teal: #00AB8E;
    --teal-light: #00BBA5;
    --ink: #1a1a1a;
    --grey: #7d8189;
    --card-dark: #050607;
    --card-light: #ffffff;
    --backdrop: #e9eef2;
  }
  * { box-sizing: border-box; margin: 0; padding: 0; }
  html, body { width: 1200px; height: 900px; overflow: hidden; }
  body {
    background: var(--backdrop);
    font-family: "Montserrat", sans-serif;
    position: relative;
  }
  .card {
    position: absolute;
    width: 600px;
    height: 343px;
    border-radius: 20px;
    overflow: hidden;
    box-shadow: 0 10px 28px rgba(0,0,0,.18);
  }
  .card-front { left: 60px; top: 60px; background: var(--card-dark); }
  .card-back { left: 540px; top: 497px; background: var(--card-light); }
  .card-wave { position: absolute; left: 0; bottom: 0; width: 600px; height: 120px; }

  .brand { display: flex; align-items: center; gap: 12px; position: absolute; }
  .brand-mark { width: 22px; height: 22px; background: var(--blue-bright); flex: none; }
  .brand-name {
    font-weight: 700;
    letter-spacing: .04em;
    text-transform: uppercase;
    color: var(--blue-bright);
    white-space: nowrap;
  }
  .card-front .brand { left: 50%; top: 104px; transform: translateX(-50%); }
  .card-front .brand-name { font-size: 34px; }
  .card-back .brand { right: 40px; top: 40px; }
  .card-back .brand-name { font-size: 26px; }

  .divider {
    position: absolute; left: 40px; right: 40px; top: 118px;
    height: 2px; background: var(--blue-bright);
  }
  .person { position: absolute; left: 40px; top: 140px; }
  .person-name {
    font-size: 24px; font-weight: 700; color: var(--blue);
    text-transform: uppercase; letter-spacing: .01em;
  }
  .person-role { font-size: 15px; color: var(--ink); margin-top: 2px; }
  .contacts { position: absolute; left: 40px; top: 214px; list-style: none; }
  .contacts li {
    display: flex; align-items: center; gap: 10px;
    font-size: 15px; color: var(--ink); line-height: 24px;
  }
  .contacts svg { width: 13px; height: 13px; flex: none; }
  .office {
    position: absolute; right: 40px; top: 188px;
    font-size: 14px; color: var(--ink);
  }
</style>
</head>
<body>

  <section class="card card-front" aria-label="Business card front">
    <div class="brand">
      <span class="brand-mark"></span>
      <span class="brand-name">Qline Telecom</span>
    </div>
    <svg class="card-wave" viewBox="0 0 600 120" preserveAspectRatio="none" aria-hidden="true">
      <path d="M0 120 L0 112 L330 112 C360 112 370 78 400 78 L600 78 L600 120 Z" fill="var(--blue)"/>
      <path d="M0 104 L335 104" stroke="var(--teal-light)" stroke-width="4"/>
    </svg>
  </section>

  <section class="card card-back" aria-label="Business card back">
    <div class="brand">
      <span class="brand-mark"></span>
      <span class="brand-name">Qline Telecom</span>
    </div>
    <div class="divider"></div>

    <div class="person">
      <p class="person-name">Mark Ellison</p>
      <p class="person-role">Director</p>
    </div>

    <ul class="contacts">
      <li>
        <svg viewBox="0 0 24 24" aria-hidden="true"><path fill="var(--blue)" d="M6.6 10.8a15.1 15.1 0 0 0 6.6 6.6l2.2-2.2c.3-.3.7-.4 1-.2 1.1.4 2.3.6 3.6.6.6 0 1 .4 1 1V20c0 .6-.4 1-1 1A17 17 0 0 1 3 4c0-.6.4-1 1-1h3.5c.6 0 1 .4 1 1 0 1.3.2 2.5.6 3.6.1.3 0 .7-.2 1z"/></svg>
        (07) 5550 1842
      </li>
      <li>
        <svg viewBox="0 0 24 24" aria-hidden="true"><rect x="2" y="5" width="20" height="14" rx="2" fill="none" stroke="var(--blue)" stroke-width="2.4"/><path d="M3 6l9 7 9-7" fill="none" stroke="var(--blue)" stroke-width="2.4"/></svg>
        qlinetelecom.com.au
      </li>
      <li>
        <svg viewBox="0 0 24 24" aria-hidden="true"><circle cx="12" cy="12" r="10" fill="none" stroke="var(--blue)" stroke-width="2.4"/><path d="M2 12h20M12 2c3 3 3 17 0 20M12 2c-3 3-3 17 0 20" fill="none" stroke="var(--blue)" stroke-width="2"/></svg>
        qlinetelecom.com.au
      </li>
    </ul>

    <p class="office">Brisbane (head) office</p>

    <svg class="card-wave" viewBox="0 0 600 120" preserveAspectRatio="none" aria-hidden="true">
      <path d="M0 120 L0 114 L330 114 C360 114 370 82 400 82 L600 82 L600 120 Z" fill="var(--blue)"/>
      <path d="M0 106 L335 106" stroke="var(--teal-light)" stroke-width="4"/>
    </svg>
  </section>

</body>
</html>
```